Home Security Company Business Card

Looking for a eye catching business card that is non traditional and stands out but yet still looks professional. It should include all the pertinent information such as name, title, address, telephone, e-mail, website address should definitely stand out and then finally the logo.

Target Market(s)

Residential and Commercial accounts mostly upscale accounts

Industry/Entity Type

Security

Contact Information for Business Card

Name
Title
Address
Office #
Cell #
E-mail
Website

Font styles to use
Serif
Sans Serif

Requirements
Must have
• Logo, two sided color configuration
Nice to have
• You decide
Should not have
• There really aren't any.

```html
<!DOCTYPE html>
<html lang="en">
<head>
<meta charset="utf-8">
<title>Harborline Security Systems – Business Card</title>
<link href="https://fonts.googleapis.com/css2?family=Tinos&family=Noto+Serif&family=Open+Sans&display=swap" rel="stylesheet">
<style>
  :root {
    --maroon: #7b1518;
    --gold: #e8b33e;
    --white: #ffffff;
    --stage: #efe7d8;
    --rule: #9a3a3c;
  }
  html, body {
    margin: 0;
    width: 1189px;
    height: 1200px;
    overflow: hidden;
    background: var(--stage);
  }
  .card {
    position: absolute;
    left: 171px;
    width: 856px;
    height: 487px;
    border-radius: 20px;
    box-shadow: 0 4px 10px rgba(0,0,0,0.25);
  }
  .card--front { top: 68px; background: var(--maroon); }
  .card--back { top: 627px; background: var(--white); }

  .brand-dot {
    position: absolute;
    border-radius: 50%;
    background: var(--gold);
  }
  .card--front .brand-dot { left: 160px; top: 157px; width: 170px; height: 170px; }
  .card--back .brand-dot { left: 170px; top: 230px; width: 60px; height: 60px; display: none; }

  .wordmark {
    position: absolute;
    font-family: "Tinos", serif;
    font-weight: 400;
    line-height: 1;
    text-align: left;
  }
  .wordmark__name { display: block; letter-spacing: -0.5px; }
  .wordmark__sub { display: block; letter-spacing: -0.6px; }

  .card--front .wordmark { left: 394px; top: 200px; color: var(--white); }
  .card--front .wordmark__name { font-size: 55px; }
  .card--front .wordmark__sub { font-size: 28px; margin-top: 2px; }
  .tagline {
    position: absolute;
    left: 395px;
    top: 291px;
    font-family: "Open Sans", sans-serif;
    font-size: 21px;
    letter-spacing: 1.6px;
    color: var(--white);
  }

  .card--back .logo-dot {
    position: absolute;
    left: 185px;
    top: 120px;
    width: 95px;
    height: 95px;
    border-radius: 50%;
    background: var(--gold);
  }
  .card--back .wordmark { left: 110px; top: 308px; color: var(--maroon); width: 290px; text-align: center; }
  .card--back .wordmark__name { font-size: 45px; }
  .card--back .wordmark__sub { font-size: 23px; margin-top: 1px; }

  .divider {
    position: absolute;
    left: 423px;
    top: 95px;
    width: 1px;
    height: 292px;
    background: var(--rule);
  }
  .contact {
    position: absolute;
    left: 463px;
    top: 97px;
    font-family: "Noto Serif", serif;
    color: var(--maroon);
  }
  .contact__name { font-size: 31px; line-height: 1; margin: 0; font-weight: 400; }
  .contact__title { font-family: "Open Sans", sans-serif; font-size: 20px; color: var(--gold); line-height: 1; margin-top: 2px; letter-spacing: 0.5px; }
  .contact__address { font-size: 21px; line-height: 29px; margin-top: 20px; }
  .contact__list { list-style: none; padding: 0; margin: 12px 0 0; font-size: 20px; }
  .contact__list li { display: flex; align-items: center; height: 31px; }
  .contact__list svg { width: 24px; height: 24px; margin-right: 15px; }
  .contact__web { font-size: 20px; color: var(--gold); margin-top: 14px; letter-spacing: 0.8px; }
</style>
</head>
<body>
  <section class="card card--front" aria-label="Card front">
    <div class="brand-dot"></div>
    <div class="wordmark">
      <span class="wordmark__name">HARBORLINE</span>
      <span class="wordmark__sub">SECURITY SYSTEMS INC.</span>
    </div>
    <div class="tagline">protect what matters most</div>
  </section>

  <section class="card card--back" aria-label="Card back">
    <div class="logo-dot"></div>
    <div class="wordmark">
      <span class="wordmark__name">HARBORLINE</span>
      <span class="wordmark__sub">SECURITY SYSTEMS INC.</span>
    </div>
    <div class="divider"></div>
    <div class="contact">
      <h1 class="contact__name">Marcus Ellery</h1>
      <div class="contact__title">Owner</div>
      <div class="contact__address">PO Box your address<br>2nd Lane, WA 0000 USA</div>
      <ul class="contact__list">
        <li>
          <svg viewBox="0 0 24 24" aria-hidden="true"><rect width="24" height="24" rx="4" fill="#e8b33e"/><path d="M6 11c0-3 12-3 12 0v1h-3v-1.5h-6V12H6z" fill="#fff"/><rect x="7.5" y="12.5" width="9" height="5.5" rx="1" fill="#fff"/></svg>
          555-014-2873
        </li>
        <li>
          <svg viewBox="0 0 24 24" aria-hidden="true"><rect width="24" height="24" rx="4" fill="#e8b33e"/><rect x="8" y="4" width="8" height="16" rx="1.5" fill="#fff"/><rect x="9.5" y="6" width="5" height="6" fill="#e8b33e"/></svg>
          +1 555-014-2873
        </li>
        <li>
          <svg viewBox="0 0 24 24" aria-hidden="true"><rect width="24" height="24" rx="4" fill="#e8b33e"/><rect x="5" y="7" width="14" height="10" fill="none" stroke="#fff" stroke-width="1.6"/><path d="M5 7l7 6 7-6M5 17l5-4.5M19 17l-5-4.5" fill="none" stroke="#fff" stroke-width="1.4"/></svg>
          info@harborlinesec.com
        </li>
      </ul>
      <div class="contact__web">www.harborlinesec.com</div>
    </div>
  </section>
</body>
</html>
```